Bramblecrest Resource Group is a recycling company. We have started a marketing campaign and would love your artwork to help us get started. We would like the fallowing to be on our postcard:
At the top please write: Now servicing businesses in the city of Industry!
Below that we would like 3 pictures.. The first is a picture of trash, the second is a our logo and at plus sign. After that would be a picture of neat baled recycled material and the last picture would be money. Below this please right the following:
- Companies choose bramblecrest resource group because:
- if it can be recycled we will find a use for it
- we pay top dollar
- starting our service is fast and easy
* All it takes is one call/email and we will handle the rest
At the bottom please put our contact information
- 800.514.2976
- delphine@bramble722.com
- bramble722.com

Thanks guys! I have attached our logo!

I am sorry for this late post,but could you not put anything on the back except for a return address which is 4187 Tillery Ave Costa Mesa, Ca 92871 Thank you! We have had a lot of trouble in the past with the post office when we put stuff on the back for some reason.

Recycling

```html
<!DOCTYPE html>
<html lang="en">
<head>
<meta charset="utf-8">
<title>Bramblecrest Resource Group – Postcard</title>
<link href="https://fonts.googleapis.com/css2?family=Arimo:wght@400;700&display=swap" rel="stylesheet">
<style>
  :root {
    --green: #5aa83c;
    --green-dark: #3f8a2a;
    --green-light: #7cc35a;
    --ink: #2b2b2b;
    --grey-text: #4a4a4a;
    --paper: #ffffff;
    --stage: #e9e6e1;
    --rule: #c9c9c9;
  }
  * { box-sizing: border-box; margin: 0; padding: 0; }
  html, body { width: 1200px; height: 900px; overflow: hidden; }
  body {
    background: var(--stage);
    font-family: "Arimo", Arial, sans-serif;
    position: relative;
    color: var(--ink);
  }
  .postcard {
    position: absolute;
    background: var(--paper);
    box-shadow: 0 6px 18px rgba(0,0,0,.25);
    overflow: hidden;
  }

  /* ---------- back side ---------- */
  .postcard--back { left: 40px; top: 40px; width: 590px; height: 380px; }
  .brand-name {
    font-weight: 700;
    color: var(--green);
    line-height: 1.05;
    display: flex;
    align-items: center;
    gap: 8px;
  }
  .brand-name .brand-dot {
    width: 16px; height: 16px; border-radius: 50%;
    background: var(--green); flex: none;
  }
  .postcard--back .brand-name { position: absolute; left: 16px; top: 40px; font-size: 20px; width: 190px; }
  .return-address {
    position: absolute; left: 210px; top: 28px;
    display: flex; align-items: flex-start; gap: 6px;
    font-size: 14px; line-height: 1.35; color: var(--ink);
  }
  .return-address .tab {
    width: 18px; height: 62px; background: var(--green);
    border-radius: 0 0 9px 9px;
    display: flex; justify-content: center; padding-top: 6px;
  }
  .stamp-box {
    position: absolute; right: 24px; top: 18px;
    width: 72px; height: 90px; border: 1px solid var(--rule);
  }
  .address-lines { position: absolute; right: 24px; top: 200px; width: 165px; }
  .address-lines span { display: block; height: 1px; background: var(--rule); margin-bottom: 27px; }

  /* ---------- front side ---------- */
  .postcard--front {
    left: 540px; top: 440px; width: 625px; height: 420px;
    background: linear-gradient(180deg, #ffffff 0%, #f2f2f2 55%, #e3e3e3 100%);
  }
  .postcard--front .brand-name { position: absolute; left: 22px; top: 34px; font-size: 22px; width: 210px; }
  .headline {
    position: absolute; right: 24px; top: 36px;
    text-align: right; font-weight: 400; font-size: 27px; line-height: 1.2;
    color: var(--green);
  }
  .headline .line-2 { display: block; padding-left: 80px; }
  .equation {
    position: absolute; left: 16px; top: 132px;
    display: flex; align-items: center;
  }
  .equation__photo {
    width: 158px; height: 158px; border-radius: 50%;
    border: 6px solid #fff;
    box-shadow: 0 2px 8px rgba(0,0,0,.35);
  }
  .photo--trash { background: radial-gradient(circle at 40% 40%, #a39a7e, #5b5a44 60%, #3c3e2f); }
  .photo--bales { background: radial-gradient(circle at 50% 45%, #d2cbd6, #a4a0b2 55%, #6f6a78); }
  .photo--money { background: radial-gradient(circle at 50% 45%, #b8c6cf, #8ea2ae 55%, #5f7584); }
  .operator {
    width: 44px; text-align: center; color: var(--green);
    font-size: 56px; font-weight: 700; line-height: 1; margin: 0 -6px;
    position: relative; z-index: 1;
  }
  .reasons {
    position: absolute; left: 14px; top: 318px; width: 282px; height: 86px;
    background: linear-gradient(180deg, var(--green-light), var(--green-dark));
    border: 2px solid #e8f3e2; border-radius: 6px;
    box-shadow: 0 2px 6px rgba(0,0,0,.3);
    color: #fff; padding: 5px 10px;
  }
  .reasons__lead { font-size: 12px; margin-bottom: 3px; }
  .reasons__list { list-style: none; font-size: 9.5px; line-height: 1.45; }
  .reasons__list li::before { content: "- "; }
  .bottom-band {
    position: absolute; left: 0; right: 0; bottom: 0; height: 36px;
    background: var(--green);
  }
  .call-to-action {
    position: absolute; right: 24px; top: 322px;
    display: flex; align-items: center; gap: 8px;
    font-size: 13px; line-height: 1.2; color: var(--grey-text);
  }
  .call-to-action .cta-icon { width: 36px; height: 36px; border-radius: 50%; background: var(--green); flex: none; }
  .contact {
    position: absolute; right: 14px; bottom: 8px;
    display: flex; gap: 10px; font-size: 12px; color: #fff;
  }
  .contact span { display: flex; align-items: center; gap: 3px; }
  .contact svg { width: 11px; height: 11px; }
</style>
</head>
<body>

  <section class="postcard postcard--back" aria-label="Postcard back">
    <div class="brand-name"><span class="brand-dot"></span><span>Bramblecrest Resource Group</span></div>
    <address class="return-address">
      <span class="tab">
        <svg width="10" height="10" viewBox="0 0 10 10" aria-hidden="true"><path d="M5 1 L9.5 5 H8 V9 H6 V6.5 H4 V9 H2 V5 H0.5 Z" fill="#fff"/></svg>
      </span>
      <span>4187 Tillery Ave<br>Costa Mesa ca 92871</span>
    </address>
    <div class="stamp-box"></div>
    <div class="address-lines"><span></span><span></span><span></span><span></span></div>
  </section>

  <section class="postcard postcard--front" aria-label="Postcard front">
    <div class="brand-name"><span class="brand-dot"></span><span>Bramblecrest Resource Group</span></div>
    <h1 class="headline">Now servicing businesses <span class="line-2">in the city of Industry!</span></h1>

    <div class="equation">
      <div class="equation__photo photo--trash" role="img" aria-label="Photo of a pile of mixed trash"></div>
      <div class="operator">+</div>
      <div class="equation__photo photo--bales" role="img" aria-label="Photo of neat bales of recycled cans"></div>
      <div class="operator">=</div>
      <div class="equation__photo photo--money" role="img" aria-label="Photo of a heap of dollar bills"></div>
    </div>

    <div class="bottom-band"></div>

    <div class="reasons">
      <p class="reasons__lead">Companies choose bramblecrest resource group because:</p>
      <ul class="reasons__list">
        <li>if it can be recycled we will find a use for it</li>
        <li>we pay top dollar</li>
        <li>starting our service is fast and easy</li>
      </ul>
    </div>

    <div class="call-to-action">
      <span class="cta-icon" role="img" aria-label="Recycling symbol"></span>
      <p>All it takes is<br>one call/email<br>and we will handle the rest</p>
    </div>

    <div class="contact">
      <span>
        <svg viewBox="0 0 12 12" aria-hidden="true"><path d="M2.5 1 L4.5 1 L5.3 3.5 L4 4.5 Q5 7 7.5 8 L8.5 6.7 L11 7.5 L11 9.5 Q11 11 9.5 11 Q1 10.5 1 2.5 Q1 1 2.5 1 Z" fill="#fff"/></svg>
        800.514.2976
      </span>
      <span>
        <svg viewBox="0 0 12 12" aria-hidden="true"><rect x="1" y="2.5" width="10" height="7" fill="none" stroke="#fff"/><path d="M1 2.5 L6 6.5 L11 2.5" fill="none" stroke="#fff"/></svg>
        delphine@bramble722.com
      </span>
      <span>
        <svg viewBox="0 0 12 12" aria-hidden="true"><circle cx="6" cy="6" r="5" fill="none" stroke="#fff"/><ellipse cx="6" cy="6" rx="2.2" ry="5" fill="none" stroke="#fff"/><path d="M1 6 H11" stroke="#fff"/></svg>
        bramble722.com
      </span>
    </div>
  </section>

</body>
</html>
```